Accounting business needs business card

I have a business card but need something better. I want the colour changed and the design to be better. I have uploaded a picture of my new sign that is grey in colour, i would like to incorporate these colours.

```html
<!DOCTYPE html>
<html lang="en">
<head>
<meta charset="utf-8">
<title>Nil Ledger — Business Card</title>
<link href="https://fonts.googleapis.com/css2?family=Montserrat:wght@500;600&family=Open+Sans:wght@400;600&display=swap" rel="stylesheet">
<style>
  :root {
    --backdrop: #e6e6e6;
    --steel-dark: #8c8d8f;
    --steel-mid: #b3b4b6;
    --steel-light: #c9cacc;
    --ink: #1f1f1f;
    --social: #5a5a5a;
    --paper: #f4f4f4;
    --teal: #1aa88a;
    --teal-faint: #cfeae3;
    --text: #333333;
    --badge-blue: #22b3e6;
    --badge-navy: #1d5aa6;
    --badge-gold: #f3cf1f;
    --badge-ring: #9a9a9a;
  }
  * { margin: 0; padding: 0; box-sizing: border-box; }
  html, body { width: 1200px; height: 960px; overflow: hidden; }
  body { background: var(--backdrop); position: relative; font-family: "Open Sans", Arial, sans-serif; }

  .card { position: absolute; left: 319px; width: 561px; height: 342px; overflow: hidden; }
  .card-front {
    top: 124px;
    background: linear-gradient(180deg, var(--steel-dark) 0%, var(--steel-light) 45%, var(--steel-mid) 100%);
  }
  .card-back { top: 504px; background: var(--paper); }
  .card svg.decor { position: absolute; left: 0; top: 0; }

  .brand-name {
    position: absolute;
    font-family: "Montserrat", Arial, sans-serif;
    font-weight: 500;
    white-space: nowrap;
    transform: translateX(-50%);
  }
  .card-front .brand-name { left: 371px; top: 208px; font-size: 29px; letter-spacing: 7px; color: var(--ink); }
  .card-back .brand-name { left: 122px; top: 106px; font-size: 21px; letter-spacing: 5px; color: var(--teal); }

  .accent-bar { position: absolute; left: 0; top: 171px; width: 14px; height: 56px; background: var(--teal); }

  .person { position: absolute; left: 40px; top: 170px; color: var(--text); }
  .person-name { font-family: "Montserrat", Arial, sans-serif; font-weight: 600; font-size: 19px; color: var(--teal); letter-spacing: 0.3px; }
  .person-role { font-size: 13px; line-height: 18px; }

  .contact-list { position: absolute; left: 40px; top: 253px; list-style: none; font-size: 13px; color: var(--text); }
  .contact-list li { display: flex; align-items: center; height: 19px; }
  .contact-list svg { width: 11px; height: 11px; margin-right: 8px; }

  .badge-caption { position: absolute; font-size: 7px; line-height: 8px; color: var(--text); text-align: center; }
  .caption-member { left: 391px; top: 289px; width: 76px; }
  .caption-agent { left: 476px; top: 297px; width: 52px; font-size: 6px; }
</style>
</head>
<body>

<section class="card card-front" aria-label="Card front">
  <svg class="decor" width="561" height="342" viewBox="0 0 561 342">
    <circle class="decor-ring" cx="36" cy="171" r="132" fill="none" stroke="#ffffff" stroke-width="8"/>
    <circle class="brand-ring" cx="371" cy="146" r="45" fill="none" stroke="var(--ink)" stroke-width="2.5"/>
    <g class="social-links" fill="var(--social)">
      <circle cx="346" cy="306" r="9"/>
      <circle cx="371" cy="306" r="9"/>
      <circle cx="397" cy="306" r="9"/>
    </g>
  </svg>
  <div class="brand-name">NIL LEDGER</div>
</section>

<section class="card card-back" aria-label="Card back">
  <svg class="decor" width="561" height="342" viewBox="0 0 561 342">
    <circle class="decor-ring" cx="497" cy="170" r="100" fill="none" stroke="var(--teal-faint)" stroke-width="8"/>
    <circle class="brand-ring" cx="122" cy="66" r="30" fill="none" stroke="var(--teal)" stroke-width="2"/>
    <g class="partner-badges">
      <circle cx="344" cy="277" r="26" fill="var(--badge-blue)"/>
      <rect x="391" y="253" width="51" height="33" fill="var(--badge-navy)"/>
      <rect x="442" y="253" width="25" height="33" fill="var(--badge-gold)"/>
      <circle cx="502" cy="272" r="23" fill="#ffffff" stroke="var(--badge-ring)" stroke-width="2"/>
    </g>
  </svg>

  <div class="brand-name">NIL LEDGER</div>
  <div class="accent-bar"></div>

  <div class="person">
    <div class="person-name">SAM WHITFIELD</div>
    <div class="person-role">CPA, MTAX, BCOM (Acc &amp; Fin)</div>
    <div class="person-role">Taxation and Business Accountant</div>
  </div>

  <ul class="contact-list">
    <li>
      <svg viewBox="0 0 12 12"><path d="M2.5 0.5 L4.5 0.5 L5.3 3.2 L4 4.3 Q5.2 6.9 7.7 8 L8.8 6.7 L11.5 7.5 L11.5 9.5 Q11.5 11.5 9.5 11.5 Q0.5 10.5 0.5 2.5 Q0.5 0.5 2.5 0.5Z" fill="var(--teal)"/></svg>
      0400 000 123
    </li>
    <li>
      <svg viewBox="0 0 12 12"><rect x="0.75" y="2" width="10.5" height="8" fill="none" stroke="var(--teal)" stroke-width="1.5"/><path d="M1 2.5 L6 6.5 L11 2.5" fill="none" stroke="var(--teal)" stroke-width="1.3"/></svg>
      sam@nilledger.com.au
    </li>
    <li>
      <svg viewBox="0 0 12 12"><circle cx="6" cy="6" r="5.2" fill="none" stroke="var(--teal)" stroke-width="1.3"/><ellipse cx="6" cy="6" rx="2.2" ry="5.2" fill="none" stroke="var(--teal)" stroke-width="1"/><path d="M1 6 H11" stroke="var(--teal)" stroke-width="1"/></svg>
      www.nilledger.com.au
    </li>
  </ul>

  <div class="badge-caption caption-member">Nil Ledger is a<br>member firm</div>
  <div class="badge-caption caption-agent">Reg. agent<br>40012345</div>
</section>

</body>
</html>
```